The Linen Loft Co

We need a business card design for our wardrobe company.
Please visit our website www.gentlelinenlofts.com to get an idea of who we are.

```html
<!DOCTYPE html>
<html lang="en">
<head>
<meta charset="utf-8">
<title>The Linen Loft Co – Business Card</title>
<link href="https://fonts.googleapis.com/css2?family=Roboto:wght@400;500;700&display=swap" rel="stylesheet">
<style>
  :root {
    --page-bg: #ecebe8;
    --card-bg: #ffffff;
    --ink: #000000;
    --ink-soft: #555555;
    --band-text: #ffffff;
  }
  html, body {
    margin: 0;
    padding: 0;
    width: 1200px;
    height: 989px;
    overflow: hidden;
    background: var(--page-bg);
    font-family: "Roboto", Arial, sans-serif;
  }
  .card {
    position: absolute;
    left: 50px;
    top: 177px;
    width: 1100px;
    height: 634px;
    background: var(--card-bg);
    box-shadow: 0 2px 8px rgba(0,0,0,0.12);
  }
  .name-band {
    position: absolute;
    left: 0;
    top: 78px;
    width: 560px;
    height: 90px;
    background: var(--ink);
    color: var(--band-text);
  }
  .person-name {
    position: absolute;
    left: 64px;
    top: 6px;
    margin: 0;
    font-size: 41px;
    font-weight: 700;
    letter-spacing: 0.2px;
  }
  .person-title {
    position: absolute;
    left: 64px;
    top: 50px;
    margin: 0;
    font-size: 28px;
    font-weight: 500;
  }
  .brand-mark {
    position: absolute;
    left: 600px;
    top: 90px;
    width: 66px;
    height: 66px;
    border: 3px solid var(--ink);
    box-sizing: border-box;
  }
  .brand {
    position: absolute;
    left: 720px;
    top: 88px;
    width: 320px;
    text-align: center;
    color: var(--ink);
  }
  .brand-name {
    margin: 0;
    font-size: 24px;
    font-weight: 500;
    text-transform: uppercase;
    letter-spacing: 0.2px;
  }
  .brand-tagline {
    margin: 10px 0 0;
    font-size: 21px;
    font-weight: 500;
  }
  .contact, .address {
    position: absolute;
    margin: 0;
    font-size: 27px;
    line-height: 34px;
    color: var(--ink-soft);
    font-style: normal;
    letter-spacing: 0.3px;
  }
  .contact {
    left: 64px;
    top: 462px;
  }
  .address {
    right: 84px;
    top: 496px;
    text-align: right;
  }
</style>
</head>
<body>
  <section class="card">
    <div class="name-band">
      <h1 class="person-name">Daniel Harwood</h1>
      <p class="person-title">President</p>
    </div>
    <div class="brand-mark"></div>
    <div class="brand">
      <p class="brand-name">The Linen Loft Co</p>
      <p class="brand-tagline">Folded with Care, Always</p>
    </div>
    <p class="contact">
      Ph. 020 7946 0182<br>
      info@gentlelinenlofts.com<br>
      www.gentlelinenlofts.com
    </p>
    <address class="address">
      Marlow Court, 42 Abbey Lane<br>
      London N4 3QT
    </address>
  </section>
</body>
</html>
```